Label Design for Climbing Chalk (fitness category)

I am looking for someone to design a front and back label for a bottle of liquid chalk. Liquid chalk is used in gyms, gymnastics, climbing to prevent your hands from getting moist and increase friction. I'm uploading some design motivations that I like.

The bottle is going to be black and I want the label to be clear. You have free reign of how you want to approach this design. Below are more specifics for the sizing:

*Attached is a picture of a competitor product (Tor Hold Liquid Chalk). Please don't use this for motivation, their label is very bad. I'm attaching a picture so that you can see what the bottle looks like.
*Attached are design motivations that I like
*The bottle is 50 ml, it's 3.75 inches tall, 2 inches wide and 1.25 inches in depth.
*The label can be square or oval (it's up to you). The size of the label needs to be 1,25 x 2.25 inches.
*Name of the product: Bravan Liquid Chalk
*Label needs to have the following Required Text. You can arrange it however you like:
- (50 ml)
- Made by USA Competitive Athletes for Athletes. Increases grip and lasts 3-4 times longer than regular chalk.
- Directions: Shake well. Squeeze some Bravan Liquid Chalk into your hand and rub your hands together. Let your hands air dry for about 10 seconds. To remove the chalk wash your hands with light soap.
Warning: Avoid contact with Eyes. Do not use on broken skin. Do not ingest. Keep out of reach of small children.
- Ingredients: Magnesium carbonate, SD Alcohol, hydroxypropylcellulose, colophonium.

Target Market(s)

Fitness, Athletes, Rock Climbers, Weight Lifters, Gymnasts, etc

Industry/Entity Type

Fitness

Font styles to use
Sans Serif

Colors

Designer to choose colors to be used in the design.

Requirements
Must have
• Please see Project Description for required text. The bottle is going to be black and I want the clear label so please be creative with the colors that would look good
Nice to have
• Please see attached branding ideas that I liked for font and colors. You don't have to strictly stick to them, these are just some of the ones I liked. Be creative and put your best foot forward.

```html
<!DOCTYPE html>
<html lang="en">
<head>
<meta charset="utf-8">
<title>Bravan Liquid Chalk – Front and Back Labels</title>
<link rel="stylesheet" href="https://fonts.googleapis.com/css2?family=Exo+2:ital,wght@0,400;0,600;0,700;0,800;1,400;1,600;1,700;1,900&display=swap">
<style>
  :root {
    --page: #ffffff;
    --label: #0b0b0b;
    --edge: #ffffff;
    --brand-red: #c8202b;
    --text: #ffffff;
    --outline: #000000;
  }
  * { margin: 0; padding: 0; box-sizing: border-box; }
  html, body {
    width: 1200px; height: 1029px; overflow: hidden;
    background: var(--page);
    font-family: "Exo 2", sans-serif;
    color: var(--text);
  }
  .canvas { position: relative; width: 1200px; height: 1029px; }

  .label {
    position: absolute;
    top: 128px;
    width: 432px; height: 784px;
    border-radius: 216px;
    background: var(--label);
    border: 5px solid var(--edge);
    box-shadow: 0 14px 28px rgba(0,0,0,.45), 0 0 2px rgba(0,0,0,.3);
    overflow: hidden;
  }
  .label--front { left: 144px; }
  .label--back { left: 652px; }

  .label > * { position: absolute; }

  .brand-name {
    color: var(--brand-red);
    font-weight: 800;
    text-align: center;
    left: 0; right: 0;
    letter-spacing: 1px;
  }

  /* Front */
  .hand-print {
    left: 30px; top: 100px;
    width: 372px; height: 560px;
    border-radius: 50%;
    background: radial-gradient(ellipse at 50% 55%, #262626 0%, #191919 50%, rgba(11,11,11,0) 72%);
  }
  .label--front .brand-name { top: 130px; font-size: 82px; line-height: 1; }
  .product-title {
    left: 0; right: 0;
    text-align: center;
    font-weight: 900; font-style: italic;
    font-size: 94px; line-height: 1;
    color: var(--text);
    letter-spacing: 1px;
    text-shadow:
      3px 0 0 var(--outline), -3px 0 0 var(--outline),
      0 3px 0 var(--outline), 0 -3px 0 var(--outline),
      2px 2px 0 var(--outline), -2px -2px 0 var(--outline),
      2px -2px 0 var(--outline), -2px 2px 0 var(--outline),
      5px 5px 0 var(--outline);
  }
  .product-title--liquid { top: 316px; }
  .product-title--chalk { top: 426px; }
  .tagline {
    left: 40px; right: 40px; top: 562px;
    text-align: center;
    font-style: italic; font-size: 17.5px; line-height: 21px;
    letter-spacing: 1px;
    text-shadow: 0 0 3px #000;
  }
  .volume {
    left: 0; right: 0; top: 694px;
    text-align: center;
    font-style: italic; font-size: 31px; letter-spacing: 1px;
  }

  /* Back */
  .label--back .brand-name { top: 66px; font-size: 50px; line-height: 1; }
  .back-title {
    left: 0; right: 0; top: 140px;
    text-align: center;
    font-weight: 900; font-style: italic;
    font-size: 34px; line-height: 1;
  }
  .info-block { left: 47px; right: 38px; }
  .info-block--directions { top: 238px; }
  .info-block--warning { top: 424px; }
  .info-heading {
    color: var(--brand-red);
    font-weight: 700; font-style: italic;
    font-size: 21px; line-height: 24px;
    letter-spacing: .5px;
  }
  .info-text {
    font-size: 17.5px; line-height: 24px;
    letter-spacing: 1px;
  }
  .divider {
    left: 75px; top: 551px;
    width: 274px; height: 9px;
    background: var(--text);
  }
  .ingredients {
    left: 30px; right: 30px; top: 590px;
    text-align: center;
  }
  .ingredients-heading {
    font-weight: 700; font-style: italic;
    font-size: 19px; line-height: 24px;
  }
  .ingredients-text {
    font-style: italic; font-size: 17.5px; line-height: 24px;
    letter-spacing: .8px;
  }
</style>
</head>
<body>
<div class="canvas">

  <section class="label label--front" aria-label="Front label">
    <div class="hand-print" role="img" aria-label="Faint textured handprint illustration behind the title"></div>
    <div class="brand-name">Bravan</div>
    <div class="product-title product-title--liquid">LIQUID</div>
    <div class="product-title product-title--chalk">CHALK</div>
    <p class="tagline">Made by USA Competitive<br>Athletes for Athletes.<br>Increases grip and lasts<br>4-3 times longer than<br>regular chalk.</p>
    <div class="volume">50 ml</div>
  </section>

  <section class="label label--back" aria-label="Back label">
    <div class="brand-name">Bravan</div>
    <div class="back-title">LIQUID CHALK</div>

    <div class="info-block info-block--directions">
      <h2 class="info-heading">Directions:</h2>
      <p class="info-text">Shake well. Squeeze some Bravan Liquid Chalk into your hand and rub your hands together. Let your hands air dry for about 10 seconds. To remove the chalk wash your hands with light soap.</p>
    </div>

    <div class="info-block info-block--warning">
      <h2 class="info-heading">Warning:</h2>
      <p class="info-text">Avoid contact with Eyes. Do not use on broken skin. Do not ingest. Keep out of reach of small children.</p>
    </div>

    <div class="divider"></div>

    <div class="ingredients">
      <h2 class="ingredients-heading">Ingredients:</h2>
      <p class="ingredients-text">Magnesium carbonate, SD Alcohol,<br>hydroxypropylcellulose,<br>colophonium.</p>
    </div>
  </section>

</div>
</body>
</html>
```